design a construction company business card

Design business card around our logo. Card must have all the typical info: name, title, address, phone, email, business name, etc. Somewhere on the card I would like to see our motto "Solid foundations... Lasting partnerships." Consider adding a splash of bright orange to the card to complement the blues and silvers/grays in the logo. We are open to metallic inks, textures, etc. We would like to see options on both light and dark backgrounds. The font in the logo is Euro Technic Extended Regular.

```html
<!DOCTYPE html>
<html lang="en">
<head>
<meta charset="utf-8">
<title>Halden Contracting – Business Card</title>
<link rel="stylesheet" href="https://fonts.googleapis.com/css2?family=Roboto:wght@300;400;500;700&display=swap">
<style>
  :root {
    --stage: #1c1c1e;
    --paper: #f6f7f9;
    --charcoal-top: #4a4a4d;
    --charcoal-bottom: #38383b;
    --back-top: #2f2f31;
    --back-bottom: #222224;
    --brand-blue: #2f6fd1;
    --accent-line: #4b5fc9;
    --text-light: #e4e4e6;
    --text-muted: #b9b9bd;
    --silver: #a9abb0;
  }
  * { box-sizing: border-box; margin: 0; padding: 0; }
  html, body { width: 1200px; height: 900px; overflow: hidden; }
  body {
    background: var(--stage);
    font-family: "Roboto", Arial, sans-serif;
    display: flex;
    flex-direction: column;
    align-items: center;
    justify-content: center;
    gap: 56px;
  }
  .card {
    width: 630px;
    height: 360px;
    border-radius: 4px;
    overflow: hidden;
    position: relative;
    box-shadow: 0 14px 30px rgba(0,0,0,.55);
  }

  /* Front */
  .card-front { background: linear-gradient(180deg, var(--charcoal-top), var(--charcoal-bottom)); }
  .front-header {
    position: absolute; left: 0; top: 0; right: 0; height: 160px;
    background: var(--paper);
    border-bottom: 3px solid var(--accent-line);
  }
  .wordmark {
    position: absolute; left: 44px; top: 50px;
    font-weight: 700; font-size: 40px; letter-spacing: 3px;
    color: var(--brand-blue);
    text-transform: uppercase;
    line-height: 1;
  }
  .wordmark-sub {
    display: block; margin-top: 8px;
    font-size: 14px; letter-spacing: 4px;
  }
  .holder { position: absolute; left: 44px; top: 188px; }
  .holder-name { color: var(--brand-blue); font-size: 24px; font-weight: 400; line-height: 1.2; }
  .holder-title { color: var(--text-light); font-size: 14px; margin-top: 2px; }
  .address { margin-top: 20px; color: var(--text-light); font-size: 13px; line-height: 1.45; font-weight: 300; }
  .contacts {
    position: absolute; right: 44px; bottom: 56px;
    list-style: none; color: var(--text-light); font-size: 13px; line-height: 1.55;
  }
  .contacts li { display: flex; align-items: center; gap: 8px; white-space: nowrap; }
  .contacts svg { width: 12px; height: 12px; fill: var(--brand-blue); flex: none; }

  /* Back */
  .card-back {
    background: linear-gradient(180deg, var(--back-top), var(--back-bottom));
    display: flex; flex-direction: column; align-items: center; justify-content: center;
  }
  .back-wordmark {
    font-weight: 700; font-size: 44px; letter-spacing: 4px; text-transform: uppercase;
    color: var(--silver); text-align: center; line-height: 1;
  }
  .back-wordmark span { display: block; font-size: 15px; letter-spacing: 5px; margin-top: 10px; }
  .motto { margin-top: 34px; color: var(--text-muted); font-size: 14px; font-weight: 300; letter-spacing: .5px; }
</style>
</head>
<body>
  <section class="card card-front" aria-label="Business card front">
    <div class="front-header">
      <div class="wordmark">Halden<span class="wordmark-sub">Contracting, Inc.</span></div>
    </div>
    <div class="holder">
      <div class="holder-name">Daniel Reeve</div>
      <div class="holder-title">Director</div>
      <div class="address">Level 2, 17 Harbour Lane<br>Easton, VIC 3100</div>
    </div>
    <ul class="contacts">
      <li><svg viewBox="0 0 24 24"><path d="M6.6 10.8a15.1 15.1 0 0 0 6.6 6.6l2.2-2.2a1 1 0 0 1 1-.25 11.4 11.4 0 0 0 3.6.57 1 1 0 0 1 1 1V20a1 1 0 0 1-1 1A17 17 0 0 1 3 4a1 1 0 0 1 1-1h3.5a1 1 0 0 1 1 1c0 1.25.2 2.45.57 3.57a1 1 0 0 1-.25 1z"/></svg>555 214 0387</li>
      <li><svg viewBox="0 0 24 24"><path d="M7 1h10a2 2 0 0 1 2 2v18a2 2 0 0 1-2 2H7a2 2 0 0 1-2-2V3a2 2 0 0 1 2-2zm0 3v14h10V4z"/></svg>555 908 6621</li>
      <li><svg viewBox="0 0 24 24"><path d="M2 5h20v14H2zm2 2v.5l8 5 8-5V7z"/></svg>info@haldenbuild.example</li>
      <li><svg viewBox="0 0 24 24"><path d="M12 2a10 10 0 1 0 0 20 10 10 0 0 0 0-20zm6.9 6h-3a15 15 0 0 0-1.4-3.9A8 8 0 0 1 18.9 8zM12 4c.8 1.2 1.5 2.5 1.9 4h-3.8c.4-1.5 1.1-2.8 1.9-4zM4.3 14a8 8 0 0 1 0-4h3.4a16 16 0 0 0 0 4zm.8 2h3a15 15 0 0 0 1.4 3.9A8 8 0 0 1 5.1 16zm3-8h-3a8 8 0 0 1 4.4-3.9A15 15 0 0 0 8.1 8zM12 20c-.8-1.2-1.5-2.5-1.9-4h3.8c-.4 1.5-1.1 2.8-1.9 4zm2.3-6H9.7a14 14 0 0 1 0-4h4.6a14 14 0 0 1 0 4zm.2 5.9a15 15 0 0 0 1.4-3.9h3a8 8 0 0 1-4.4 3.9zm1.8-5.9a16 16 0 0 0 0-4h3.4a8 8 0 0 1 0 4z"/></svg>www.haldenbuild.example</li>
    </ul>
  </section>

  <section class="card card-back" aria-label="Business card back">
    <div class="back-wordmark">Halden<span>Contracting, Inc.</span></div>
    <p class="motto">Solid foundations... Lasting partnerships</p>
  </section>
</body>
</html>
```